Laser Tattoo Removal Business Cards

We are looking for a professional business card design for a laser tattoo removal business. Ideally looking for a black business card design. The name of the business is Brightline Tattoo Removal. We place our cards at local tattoo shops so we ideally are looking for something trendy/edgy to draw both male and female clientele in.

Target Market(s)

Male/Female ages 18-60

Contact Information for Business Card

black background ideally.. hoping to stay within greys, whites and black

Font styles to use
Serif
Sans Serif

Colors
121212
a9a9a9
5c5c5c
f5f5f5
ffffff
7f7f7f
606060
848484
9d9d9d

Requirements
Must have
• Employee Info:
• Melissa Thornbury
• Chief Executive Offer
• m: 919.537.2846
• w: 919.362.4178
• f: 919.685.3907
• mthornbury@brightlinetattooremoval.example
• Address:
• 4615 Oakmere Pkwy, Suite 210
• Raleigh, NC 27654
• Website:
• www.brightlinetattooremoval.example
Nice to have
• Myabe business name on back or logo on back and employee info on the front

```html
<!DOCTYPE html>
<html lang="en">
<head>
<meta charset="utf-8">
<title>Brightline Tattoo Removal – Business Cards</title>
<link href="https://fonts.googleapis.com/css2?family=Raleway:wght@400;500;600&display=swap" rel="stylesheet">
<style>
  :root {
    --stage: #2a2a2a;
    --card: #ffffff;
    --ink: #121212;
    --ink-soft: #5c5c5c;
    --ink-mid: #606060;
    --photo-light: #f5f5f5;
    --photo-mid: #9d9d9d;
    --photo-dark: #2e2e2e;
  }
  * { margin: 0; padding: 0; box-sizing: border-box; }
  html, body { width: 1200px; height: 960px; overflow: hidden; }
  body {
    background: var(--stage);
    font-family: "Raleway", Arial, sans-serif;
    color: var(--ink);
    position: relative;
  }
  .card {
    position: absolute;
    left: 281px;
    width: 655px;
    height: 374px;
    background: var(--card);
    border-radius: 20px;
    overflow: hidden;
  }
  .card--front { top: 80px; }
  .card--back { top: 506px; }

  .brand-name {
    position: absolute;
    width: 200px;
    font-size: 25px;
    font-weight: 500;
    letter-spacing: 2px;
    line-height: 1.25;
    text-transform: uppercase;
    color: var(--ink);
    text-align: center;
  }
  .card--front .brand-name { left: 42px; top: 62px; }
  .card--back .brand-name { right: 38px; top: 48px; z-index: 2; }

  .person {
    position: absolute;
    right: 40px;
    top: 157px;
    text-align: right;
  }
  .person__name {
    font-size: 22px;
    font-weight: 600;
    letter-spacing: 0.3px;
    text-transform: uppercase;
    color: var(--ink);
  }
  .person__title {
    margin-top: 6px;
    font-size: 17px;
    color: var(--ink-soft);
  }

  .contacts {
    position: absolute;
    left: 42px;
    top: 254px;
    list-style: none;
  }
  .contacts li {
    display: flex;
    align-items: center;
    height: 22px;
    font-size: 15px;
    color: var(--ink-soft);
  }
  .contacts svg {
    width: 12px;
    height: 12px;
    margin-right: 9px;
    fill: var(--ink);
    flex: none;
  }

  .address {
    position: absolute;
    right: 40px;
    top: 296px;
    text-align: right;
    font-size: 15px;
    line-height: 22px;
    color: var(--ink-soft);
    font-style: normal;
  }

  .photo {
    position: absolute;
    left: 0;
    right: 0;
    top: 122px;
    bottom: 0;
    background: linear-gradient(to bottom, var(--card) 0%, var(--photo-light) 18%, #d6d6d6 45%, var(--photo-mid) 72%, var(--photo-dark) 100%);
  }
</style>
</head>
<body>

  <section class="card card--front">
    <div class="brand-name">Brightline Tattoo Removal</div>

    <div class="person">
      <div class="person__name">Melissa Thornbury</div>
      <div class="person__title">Chief Executive Offer</div>
    </div>

    <ul class="contacts">
      <li>
        <svg viewBox="0 0 12 12" aria-hidden="true"><path d="M3 0h6a1 1 0 0 1 1 1v10a1 1 0 0 1-1 1H3a1 1 0 0 1-1-1V1a1 1 0 0 1 1-1zm.5 1.5v8h5v-8z"/></svg>
        919.537.2846
      </li>
      <li>
        <svg viewBox="0 0 12 12" aria-hidden="true"><path d="M2.5 0.5l2 2.5-1.2 1.4c.8 1.7 2 2.9 3.6 3.7l1.4-1.2 2.5 2-1.3 2.4C4.8 11 1 7.2.5 2z"/></svg>
        919.362.4178
      </li>
      <li>
        <svg viewBox="0 0 12 12" aria-hidden="true"><path d="M3 0h6v3H3zM1 4h10a1 1 0 0 1 1 1v4H9v3H3V9H0V5a1 1 0 0 1 1-1zm3 4v3h4V8z"/></svg>
        919.685.3907
      </li>
      <li>
        <svg viewBox="0 0 12 12" aria-hidden="true"><path d="M0 2h12v1L6 7 0 3zm0 2.2l6 4 6-4V10H0z"/></svg>
        mthornbury@brightlinetattooremoval.example
      </li>
      <li>
        <svg viewBox="0 0 12 12" aria-hidden="true"><path d="M6 0a6 6 0 1 0 0 12A6 6 0 0 0 6 0zm0 1c.7.8 1.2 2 1.4 3.5H4.6C4.8 3 5.3 1.8 6 1zM1.1 5.5h2.5c0 1 .1 1.9.4 2.8H1.7a5 5 0 0 1-.6-2.8zm3.5 0h2.8c0 1-.2 2-.5 2.8H5.1c-.3-.8-.5-1.8-.5-2.8zm3.8 0h2.5c0 1-.2 1.9-.6 2.8H8c.3-.9.4-1.8.4-2.8zM5.4 9.3h1.2L6 10.8z"/></svg>
        www.brightlinetattooremoval.example
      </li>
    </ul>

    <address class="address">
      4615 Oakmere Pkwy, Suite 210<br>
      Raleigh, NC 27654
    </address>
  </section>

  <section class="card card--back">
    <div class="brand-name">Brightline Tattoo Removal</div>
    <div class="photo" role="img" aria-label="Photo of a technician in gloves removing a script tattoo from a client's hip with a laser handpiece"></div>
  </section>

</body>
</html>
```